BOLD & MINIMALIST DESIGN NEEDED

We want a very bold but minimalistic business card design that is impactful and utilizes both sides of the business card. Our current logo is included for your use.

We want bold fonts and good use of negative space. We don't want the logo to overpower the design.

Target Market(s)

Professionals who are building new commercial buildings.

Industry/Entity Type

Construction

Contact Information for Business Card

Name, Title, email, office phone, cell phone, website

Font styles to use
Serif
Sans Serif

Requirements
Must have
• Bold design!

```html
<!DOCTYPE html>
<html lang="en">
<head>
<meta charset="utf-8">
<title>Ridgeline Design + Build — Business Card</title>
<link href="https://fonts.googleapis.com/css2?family=Montserrat:wght@400;500;800&family=Poppins:wght@400;500;600&display=swap" rel="stylesheet">
<style>
  :root {
    --stage: #2c2c2c;
    --card-black: #050505;
    --card-white: #ffffff;
    --ink: #141414;
    --green: #7cc242;
    --muted: #3a3a3a;
  }
  * { box-sizing: border-box; margin: 0; padding: 0; }
  html, body { width: 1200px; height: 875px; overflow: hidden; }
  body {
    background: var(--stage);
    font-family: "Poppins", sans-serif;
    position: relative;
  }
  .card {
    position: absolute;
    top: 289px;
    width: 520px;
    height: 297px;
    border-radius: 18px;
    overflow: hidden;
    box-shadow: 0 18px 40px rgba(0,0,0,0.45);
  }
  .card--front { left: 50px; background: var(--card-black); }
  .card--back { left: 630px; background: var(--card-white); }

  .wordmark {
    display: flex;
    align-items: center;
    gap: 10px;
    font-family: "Montserrat", sans-serif;
    font-weight: 800;
    text-transform: uppercase;
    letter-spacing: 0.02em;
  }
  .wordmark__mark { width: 16px; height: 16px; background: var(--green); flex: none; }

  .card--front .wordmark {
    position: absolute;
    left: 0; right: 0; top: 50%;
    transform: translateY(-50%);
    justify-content: center;
    color: #fff;
    font-size: 26px;
  }

  .card--back .wordmark {
    position: absolute;
    left: 36px; top: 112px;
    color: var(--ink);
    font-size: 22px;
  }

  .person {
    position: absolute;
    right: 32px; top: 30px;
    text-align: right;
  }
  .person__name {
    font-family: "Montserrat", sans-serif;
    font-weight: 800;
    color: var(--green);
    font-size: 21px;
    line-height: 1.1;
  }
  .person__title { font-size: 11px; color: var(--ink); margin-top: 2px; }

  .contacts {
    position: absolute;
    left: 36px; bottom: 30px;
    list-style: none;
    font-size: 12px;
    color: var(--muted);
    line-height: 1.65;
  }
  .contacts li { display: flex; align-items: center; gap: 8px; }
  .contacts svg { width: 11px; height: 11px; fill: var(--green); flex: none; }

  .band {
    position: absolute;
    right: 0; bottom: 0;
    width: 300px; height: 200px;
  }
</style>
</head>
<body>
  <section class="card card--front" aria-label="Card front">
    <div class="wordmark"><span class="wordmark__mark"></span>Ridgeline Design + Build</div>
  </section>

  <section class="card card--back" aria-label="Card back">
    <div class="wordmark"><span class="wordmark__mark"></span>Ridgeline Design + Build</div>

    <div class="person">
      <p class="person__name">Daniel Reyes</p>
      <p class="person__title">CEO &amp; Founder</p>
    </div>

    <ul class="contacts">
      <li><svg viewBox="0 0 24 24"><path d="M6.6 10.8a15 15 0 0 0 6.6 6.6l2.2-2.2a1 1 0 0 1 1-.25 11.4 11.4 0 0 0 3.6.57 1 1 0 0 1 1 1V20a1 1 0 0 1-1 1A17 17 0 0 1 3 4a1 1 0 0 1 1-1h3.5a1 1 0 0 1 1 1c0 1.25.2 2.45.57 3.57a1 1 0 0 1-.25 1z"/></svg>(555) 214-0398</li>
      <li><svg viewBox="0 0 24 24"><path d="M4 8h16v12H4zM7 3h10v4H7zm2 8h2v2H9zm4 0h2v2h-2zm-4 4h2v2H9zm4 0h2v2h-2z"/></svg>1-800-555-0142</li>
      <li><svg viewBox="0 0 24 24"><path d="M2 5h20v14H2zm2 2v.5l8 5 8-5V7z"/></svg>info@ridgelinebuild.com</li>
      <li><svg viewBox="0 0 24 24"><circle cx="12" cy="12" r="10"/></svg>www.ridgelinebuild.com</li>
    </ul>

    <svg class="band" viewBox="0 0 300 200" preserveAspectRatio="none" aria-hidden="true">
      <path d="M0 200 C90 175 150 95 300 60 L300 200 Z" fill="var(--card-black)"/>
    </svg>
  </section>
</body>
</html>
```